Bramblewood Card Company Business Cards

We are a trading card store with Glimmorax, sports and other TCG cards, we need a business card design that encompasses a clean cut, modern style with a retro flare. website is bramblewoodcardco.com for reference. Can utilize a comic book era feel or a more modern outdoor feel to utilize the "Pacific Northwest" elements of tress, mountains, etc.

Industry/Entity Type

Trading cards and collectibles

Contact Information for Business Card

business name, email address, phone number, name, owner job title

Font styles to use
Sans Serif

```html
<!DOCTYPE html>
<html lang="en">
<head>
<meta charset="utf-8">
<title>Bramblewood Card Company – Business Cards</title>
<link href="https://fonts.googleapis.com/css2?family=Montserrat:wght@400;500;700&display=swap" rel="stylesheet">
<style>
  :root {
    --backdrop: #d4d7d7;
    --paper: #f7f7f5;
    --charcoal: #474747;
    --slate-text: #3c3c3c;
    --teal: #1a9ec4;
    --cyan: #12b6da;
    --shadow: rgba(0, 0, 0, 0.18);
  }
  * { box-sizing: border-box; margin: 0; padding: 0; }
  html, body {
    width: 1200px; height: 829px; overflow: hidden;
    background: var(--backdrop);
    font-family: "Montserrat", Arial, sans-serif;
  }
  .sheet {
    position: relative; width: 1200px; height: 829px;
    display: flex; align-items: center; justify-content: center; gap: 40px;
  }
  .card {
    position: relative; width: 540px; height: 310px;
    box-shadow: 0 14px 30px var(--shadow);
    overflow: hidden;
  }
  .card--front { background: var(--paper); }
  .card--back { background: var(--cyan); display: flex; align-items: center; justify-content: center; }

  .brand-mark {
    display: flex; align-items: center; gap: 8px;
    color: var(--charcoal); font-weight: 700; text-transform: uppercase;
    letter-spacing: 1px; line-height: 1.15; text-align: center;
  }
  .brand-mark__square { width: 14px; height: 14px; background: var(--charcoal); flex: none; }
  .card--front .brand-mark {
    position: absolute; left: 300px; top: 62px; transform: translateX(-50%);
    font-size: 15px; width: 230px;
  }
  .card--back .brand-mark { font-size: 26px; width: 340px; }

  .name-band {
    position: absolute; left: 0; top: 130px; width: 258px; height: 92px;
    background: var(--charcoal); padding: 20px 0 0 26px;
  }
  .name-band__name { color: var(--teal); font-weight: 500; font-size: 24px; letter-spacing: 1px; text-transform: uppercase; }
  .name-band__title { color: #cfcfcf; font-size: 13px; margin-top: 4px; }

  .contact-band {
    position: absolute; left: 272px; top: 190px; width: 268px; height: 92px;
    background: var(--teal); padding: 12px 0 0 18px;
    list-style: none;
  }
  .contact-band li {
    display: flex; align-items: center; gap: 8px;
    color: #f4f9fb; font-size: 12.5px; line-height: 23px;
  }
  .contact-band svg { width: 12px; height: 12px; flex: none; }

  .address {
    position: absolute; left: 26px; top: 236px;
    color: var(--slate-text); font-size: 12.5px; letter-spacing: 0.3px;
    width: 240px; line-height: 1.5;
  }
</style>
</head>
<body>
<main class="sheet">
  <section class="card card--front" aria-label="Business card front">
    <div class="brand-mark">
      <span class="brand-mark__square"></span>
      <span>Bramblewood Card Company</span>
    </div>

    <div class="name-band">
      <p class="name-band__name">Dalen Marsh</p>
      <p class="name-band__title">CEO/Founder</p>
    </div>

    <ul class="contact-band">
      <li>
        <svg viewBox="0 0 12 12" aria-hidden="true"><path d="M2.5 1h2l1 3-1.3 1a6 6 0 0 0 2.8 2.8L8 6.5l3 1v2A1.5 1.5 0 0 1 9.5 11 8.5 8.5 0 0 1 1 2.5 1.5 1.5 0 0 1 2.5 1z" fill="#fff"/></svg>
        (123) 456 7890
      </li>
      <li>
        <svg viewBox="0 0 12 12" aria-hidden="true"><rect x="0.5" y="2" width="11" height="8" fill="#fff"/><path d="M0.5 2 6 6.5 11.5 2" fill="none" stroke="#1a9ec4" stroke-width="1"/></svg>
        info@bramblewoodcardco.com
      </li>
      <li>
        <svg viewBox="0 0 12 12" aria-hidden="true"><g fill="none" stroke="#fff" stroke-width="1"><circle cx="6" cy="6" r="5"/><ellipse cx="6" cy="6" rx="2.2" ry="5"/><path d="M1 6h10M2 3.3h8M2 8.7h8"/></g></svg>
        www.bramblewoodcardco.com
      </li>
    </ul>

    <p class="address">P.O. Box 2145 Street Country Name AB 8542</p>
  </section>

  <section class="card card--back" aria-label="Business card back">
    <div class="brand-mark">
      <span class="brand-mark__square"></span>
      <span>Bramblewood Card Company</span>
    </div>
  </section>
</main>
</body>
</html>
```